Elegant Business Card for Technology Company

Client is a supplier of innovative industrial communications and automation equipment since 2002. This contest is to gather fresh ideas for a redesign of the existing business card. Client is looking for design that best communicates tagline "Industrial Networking and Computing Specialist".

Design submissions should look modern, clean, elegant and professional. It should not be cluttered. Use white as the primary colour. Orange and black as secondary colour. Refer to jpeg File 1 on the current design.

Fonts used by Client used include Arial Regular, Arial Black, Roboto Regular, Roboto Black and Lato.

The winning design will be sent for offset printing using super white 250gsm artcard paper (open for suggestions).

Target Market(s)

System Engineers, Project Managers, Purchasing Managers from companies providing engineering services for Smart Cities.

Industry/Entity Type

Information Technology

Contact Information for Business Card

Refer to PDF File 3 for Business Card Details. Priority of short contact information would be as follows Name > Job Title > Email > Mobile > Web > Tel > Fax > Business Address >UEN (UEN represents company registration number)

Font styles to use
Sans Serif

Colors
ffffff
f37122
000000
5c5c5c

Requirements
Must have
• Refer to AI File 2 (Company Logo) & PDF File 3 (Information on Namecard)
Should not have
• No QR codes
• No Social Media Icons
• Do not create full Black or Orange colour background

```html
<!DOCTYPE html>
<html lang="en">
<head>
<meta charset="utf-8">
<title>KVR Business Card</title>
<link href="https://fonts.googleapis.com/css2?family=Arimo:wght@400;700&display=swap" rel="stylesheet">
<style>
  :root {
    --white: #ffffff;
    --orange: #f37122;
    --orange-deep: #d45d16;
    --black: #000000;
    --grey: #5c5c5c;
    --ink: #2b2b2b;
    --stage: #e8e5e0;
  }
  * { box-sizing: border-box; margin: 0; padding: 0; }
  html, body {
    width: 1200px; height: 950px; overflow: hidden;
    background: var(--stage);
    font-family: "Arimo", Arial, sans-serif;
  }
  .sheet {
    position: relative; width: 1200px; height: 950px;
    display: flex; flex-direction: column; align-items: center;
    justify-content: center; gap: 50px;
  }
  .card {
    position: relative; width: 700px; height: 400px; overflow: hidden;
    background: var(--white);
    box-shadow: 0 6px 18px rgba(0,0,0,0.18);
  }

  /* Back: white card with an orange brand band */
  .brand-band {
    position: absolute; left: 0; right: 0; top: 0; height: 230px;
    background: linear-gradient(135deg, var(--orange) 0%, var(--orange-deep) 100%);
  }
  .brand {
    position: absolute; display: flex; align-items: center; gap: 16px;
  }
  .brand-dot { border-radius: 50%; flex: none; }
  .brand-name { font-weight: 700; letter-spacing: 2px; line-height: 1; }

  .card-back .brand { left: 0; right: 0; top: 60px; justify-content: center; }
  .card-back .brand-dot { width: 110px; height: 110px; background: var(--white); }
  .card-back .brand-name { font-size: 76px; color: var(--white); }
  .tagline {
    position: absolute; left: 0; right: 0; top: 258px;
    text-align: center; font-size: 18px; line-height: 27px; letter-spacing: 0.5px;
    color: var(--grey);
  }
  .tagline strong { color: var(--orange); font-weight: 700; }

  /* Front */
  .name-band {
    position: absolute; left: 0; top: 45px; width: 420px; height: 72px;
    background: var(--black); padding: 12px 0 0 40px;
  }
  .person-name { color: var(--orange); font-size: 24px; font-weight: 700; line-height: 28px; }
  .person-title { color: var(--white); font-size: 16px; line-height: 22px; }
  .card-front .brand { right: 36px; top: 60px; gap: 12px; }
  .card-front .brand-dot { width: 120px; height: 120px; background: var(--orange); }
  .card-front .brand-name { font-size: 72px; color: var(--ink); }

  .contact-list {
    position: absolute; left: 40px; top: 205px; list-style: none;
    font-size: 17px; line-height: 25px; color: var(--ink);
  }
  .contact-list li { display: flex; align-items: center; gap: 10px; }
  .contact-list svg { width: 15px; height: 15px; fill: var(--orange); flex: none; }

  .address {
    position: absolute; right: 40px; bottom: 36px; text-align: right;
    font-style: normal; font-size: 17px; line-height: 23px; color: var(--grey);
  }
</style>
</head>
<body>
<main class="sheet">

  <section class="card card-back" aria-label="Card back">
    <div class="brand-band"></div>
    <div class="brand">
      <span class="brand-dot"></span>
      <span class="brand-name">KVR</span>
    </div>
    <p class="tagline">
      <strong>Industrial Networking &amp; Computing Specialist</strong><br>
      Ethernet / Wireless / Cellular<br>
      Routing / Serial / Fieldbus Connectivity<br>
      Control &amp; Remote Automation
    </p>
  </section>

  <section class="card card-front" aria-label="Card front">
    <div class="name-band">
      <p class="person-name">Daniel Koh</p>
      <p class="person-title">Sales Manager</p>
    </div>
    <div class="brand">
      <span class="brand-dot"></span>
      <span class="brand-name">KVR</span>
    </div>

    <ul class="contact-list">
      <li>
        <svg viewBox="0 0 16 16" aria-hidden="true"><path d="M3 1h3l1.5 4-2 1.3a9 9 0 0 0 4.2 4.2L11 8.5l4 1.5v3c0 1-1 2-2 2A13 13 0 0 1 1 3c0-1 1-2 2-2z"/></svg>
        +65 6123 4560
      </li>
      <li>
        <svg viewBox="0 0 16 16" aria-hidden="true"><path d="M4 1h7v4H4zM1 6h14v7h-2v2H3v-2H1zM5 10v3h6v-3z"/></svg>
        +65 9123 4567
      </li>
      <li>
        <svg viewBox="0 0 16 16" aria-hidden="true"><path d="M4 1h8v14H4zM6 3v9h4V3z"/></svg>
        +65 6123 4561
      </li>
      <li>
        <svg viewBox="0 0 16 16" aria-hidden="true"><path d="M1 3h14v1L8 9 1 4zM1 6l7 5 7-5v7H1z"/></svg>
        sales@kvr.com.sg
      </li>
    </ul>

    <address class="address">
      24 Kallang Way<br>
      Tech Hub #05-12 (Lobby B)<br>
      Singapore 349210<br>
      www.kvr.com.sg
    </address>
  </section>

</main>
</body>
</html>
```